Business card design for Virtual Assistance company

I need a business card designed for my virtual assistance company. We are a small company who services primarily C-level executive clients. The card needs to be double sided with the following contact information on the back:
Melissa Thornbury
Owner/CEO
info@rkpadvisory.net
www.rkpadvisory.net
555.302.9817

The front side should just have the company name incorporated: "RKP Advisory" and "virtual assistance"

The card should be simplistic, but eye catching and should speak to high level executives. Our primary focus areas consist of executive assistance and government contracting.

Target Market(s)

CEOs and executives

Contact Information for Business Card

see project description. phone, email, website.

Colors

Designer to choose only greyscale colors for use in the design.

```html
<!DOCTYPE html>
<html lang="en">
<head>
<meta charset="utf-8">
<title>RKP Advisory – Business Card</title>
<link rel="stylesheet" href="https://fonts.googleapis.com/css2?family=Playfair+Display:wght@400;700&family=Montserrat:wght@400;500&display=swap">
<style>
  :root {
    --backdrop: #d9d6d2;
    --card-white: #ffffff;
    --card-black: #0f0f10;
    --ink: #1e1e1e;
    --ink-soft: #3a3a3a;
    --paper-text: #f4f4f4;
    --pattern-light: #4a4a4c;
    --pattern-dark: #0c0c0d;
  }
  html, body {
    margin: 0;
    padding: 0;
    width: 900px;
    height: 1200px;
    overflow: hidden;
    background: var(--backdrop);
  }
  .canvas {
    position: relative;
    width: 900px;
    height: 1200px;
  }
  .card {
    position: absolute;
    border-radius: 24px;
    overflow: hidden;
    box-shadow: 0 6px 14px rgba(0,0,0,0.25);
  }
  .card-front {
    left: 80px; top: 131px; width: 742px; height: 441px;
    background: var(--card-white);
    color: var(--ink);
  }
  .card-back {
    left: 78px; top: 638px; width: 744px; height: 440px;
    background: var(--card-black);
  }
  .company-name {
    position: absolute;
    left: 28px; top: 50px;
    margin: 0;
    font-family: "Playfair Display", serif;
    font-weight: 400;
    font-size: 38px;
    line-height: 1;
    color: var(--ink);
  }
  .company-tagline {
    position: absolute;
    left: 70px; top: 102px;
    margin: 0;
    font-family: "Playfair Display", serif;
    font-size: 17px;
    letter-spacing: 0.5px;
    line-height: 1;
  }
  .person {
    position: absolute;
    right: 44px; top: 46px;
    text-align: right;
  }
  .person-name {
    margin: 0;
    font-family: "Playfair Display", serif;
    font-weight: 700;
    font-size: 25px;
    line-height: 1.1;
  }
  .person-role {
    margin: 2px 0 0;
    font-family: "Montserrat", sans-serif;
    font-size: 15px;
  }
  .contact-list {
    position: absolute;
    left: 28px; top: 318px;
    margin: 0; padding: 0;
    list-style: none;
    font-family: "Montserrat", sans-serif;
    font-size: 15px;
    color: var(--ink);
  }
  .contact-list li {
    display: flex;
    align-items: center;
    height: 28px;
  }
  .contact-list svg {
    width: 15px; height: 15px;
    margin-right: 10px;
    fill: var(--ink);
  }
  .front-brand {
    position: absolute;
    right: 44px; top: 340px;
    margin: 0;
    font-family: "Playfair Display", serif;
    font-weight: 400;
    font-size: 50px;
    line-height: 1;
    color: var(--ink-soft);
  }
  .back-pattern {
    position: absolute;
    inset: 0;
    background: linear-gradient(100deg, var(--pattern-light) 0%, #242426 28%, var(--pattern-dark) 55%, #161617 100%);
  }
  .back-brand {
    position: absolute;
    right: 82px; top: 292px;
    margin: 0;
    font-family: "Playfair Display", serif;
    font-weight: 400;
    font-size: 34px;
    line-height: 1;
    color: var(--paper-text);
  }
</style>
</head>
<body>
<main class="canvas">
  <section class="card card-front">
    <h1 class="company-name">RKP Advisory</h1>
    <p class="company-tagline">VIRTUAL ASSISTANCE</p>

    <div class="person">
      <p class="person-name">Melissa Thornbury</p>
      <p class="person-role">Owner/CEO</p>
    </div>

    <ul class="contact-list">
      <li>
        <svg viewBox="0 0 24 24" aria-hidden="true"><path d="M6.6 10.8a15.1 15.1 0 0 0 6.6 6.6l2.2-2.2a1 1 0 0 1 1-.25 11.4 11.4 0 0 0 3.6.57 1 1 0 0 1 1 1V20a1 1 0 0 1-1 1A17 17 0 0 1 3 4a1 1 0 0 1 1-1h3.5a1 1 0 0 1 1 1c0 1.25.2 2.45.57 3.6a1 1 0 0 1-.25 1z"/></svg>
        555.302.9817
      </li>
      <li>
        <svg viewBox="0 0 24 24" aria-hidden="true"><path d="M3 6h18v12H3z"/><path d="M3 6l9 7 9-7" stroke="#fff" stroke-width="1.6" fill="none"/></svg>
        info@rkpadvisory.net
      </li>
      <li>
        <svg viewBox="0 0 24 24" aria-hidden="true"><circle cx="12" cy="12" r="10"/><path d="M7 8c2 0 3 1 3 3s-2 2-2 4 1 3 1 4M15 5c-1 2 0 3 2 3s2 2 1 4" stroke="#fff" stroke-width="1.6" fill="none"/></svg>
        www.rkpadvisory.net
      </li>
    </ul>

    <p class="front-brand">RKP Advisory</p>
  </section>

  <section class="card card-back">
    <div class="back-pattern" role="img" aria-label="Dark grey background with a soft light sheen across the card back"></div>
    <p class="back-brand">RKP Advisory</p>
  </section>
</main>
</body>
</html>
```